Healthcare and Professional IT Services Company need a redesigned business card

We are a IT Services company that targets small medical practices and professional business such as Attorneys, Accounts, Architects etc. We want to communicate a professional yet friendly image using recent logo redesign here on ArtHarbor. Like to see the colors blue and orange in the design. Must use the Tall Pine Computing as displayed in the new logo - then also want to incorporate the fish logo as well.

Target Market(s)

Small medical and professional services

Industry/Entity Type

It Company

Contact Information for Business Card

The usual stuff, place for name address phone website. Also maybe our tagline which is "rooted in technology"

Requirements
Must have
• My new logo and the fish somewhere on the card

```html
<!DOCTYPE html>
<html lang="en">
<head>
<meta charset="utf-8">
<title>Tall Pine Computing – Business Card</title>
<link rel="stylesheet" href="https://fonts.googleapis.com/css2?family=Montserrat:wght@700&family=Questrial&display=swap">
<style>
  :root {
    --backdrop: #efe6d6;
    --card: #ffffff;
    --brand-blue: #1a9ad6;
    --deep-blue: #1a6fb5;
    --accent-orange: #f39a2b;
    --ink: #4a4a4a;
    --card-shadow: rgba(60, 45, 25, 0.28);
  }
  * { box-sizing: border-box; margin: 0; padding: 0; }
  html, body { width: 1189px; height: 1200px; overflow: hidden; }
  body {
    background: var(--backdrop);
    font-family: "Questrial", sans-serif;
    position: relative;
  }
  .card {
    position: absolute;
    left: 171px;
    width: 856px;
    height: 487px;
    background: var(--card);
    border-radius: 20px;
    box-shadow: 6px 8px 14px var(--card-shadow);
  }
  .card--front { top: 68px; }
  .card--back { top: 627px; }

  .brand-mark {
    position: absolute;
    border-radius: 50%;
    background: var(--brand-blue);
  }
  .brand-name {
    position: absolute;
    font-family: "Questrial", sans-serif;
    color: var(--brand-blue);
    font-weight: 400;
    line-height: 1;
    white-space: nowrap;
  }
  .tagline {
    position: absolute;
    color: var(--deep-blue);
    line-height: 1;
    white-space: nowrap;
  }

  /* Front */
  .card--front .brand-mark { left: 140px; top: 181px; width: 130px; height: 130px; }
  .card--front .brand-name { left: 343px; top: 222px; font-size: 40px; }
  .card--front .tagline { left: 343px; top: 300px; font-size: 24px; letter-spacing: 0.32em; }

  /* Back */
  .card--back .brand-mark { left: 149px; top: 104px; width: 130px; height: 130px; }
  .card--back .brand-name { left: 214px; top: 262px; font-size: 26px; transform: translateX(-50%); }
  .card--back .tagline { left: 214px; top: 336px; font-size: 25px; transform: translateX(-50%); }

  .divider {
    position: absolute;
    left: 407px;
    top: 85px;
    width: 2px;
    height: 304px;
    background: var(--accent-orange);
    opacity: 0.7;
  }
  .contact__name {
    position: absolute;
    left: 462px;
    top: 100px;
    font-family: "Montserrat", sans-serif;
    font-weight: 700;
    font-size: 30px;
    color: var(--brand-blue);
    line-height: 1;
  }
  .contact__role {
    position: absolute;
    left: 462px;
    top: 133px;
    font-size: 25px;
    line-height: 1;
    color: var(--ink);
  }
  .contact__address {
    position: absolute;
    left: 462px;
    top: 214px;
    font-size: 26px;
    line-height: 29px;
    font-style: normal;
    color: var(--ink);
    white-space: nowrap;
  }
  .contact__lines {
    position: absolute;
    left: 462px;
    top: 292px;
    list-style: none;
    color: var(--ink);
  }
  .contact__lines li {
    display: flex;
    align-items: center;
    gap: 9px;
    font-size: 25px;
    height: 27px;
    white-space: nowrap;
  }
  .contact__icon { width: 23px; height: 23px; flex: none; }
</style>
</head>
<body>
  <section class="card card--front" aria-label="Card front">
    <span class="brand-mark" aria-hidden="true"></span>
    <span class="brand-name">Tall Pine Computing</span>
    <p class="tagline">rooted in technology</p>
  </section>

  <section class="card card--back" aria-label="Card back">
    <span class="brand-mark" aria-hidden="true"></span>
    <span class="brand-name">Tall Pine Computing</span>
    <p class="tagline">rooted in technology</p>
    <div class="divider"></div>
    <h1 class="contact__name">Employee Name</h1>
    <p class="contact__role">Director</p>
    <address class="contact__address">P.O. Box 000<br>Cedar Ridge, 2nd Land,USA</address>
    <ul class="contact__lines">
      <li>
        <svg class="contact__icon" viewBox="0 0 22 22" aria-hidden="true">
          <rect width="22" height="22" rx="3" fill="#1a9ad6"/>
          <path d="M7 5c1 0 2 2 2 3s-1 1-1 2c0 1 2 4 3 4s1-1 2-1 3 1 3 2-1 2-2 2C10 17 5 12 5 7c0-1 1-2 2-2z" fill="#fff"/>
        </svg>
        <span>0123 456 789</span>
      </li>
      <li>
        <svg class="contact__icon" viewBox="0 0 22 22" aria-hidden="true">
          <rect width="22" height="22" rx="3" fill="#1a9ad6"/>
          <rect x="4" y="6" width="14" height="10" fill="none" stroke="#fff" stroke-width="1.5"/>
          <path d="M4 6l7 6 7-6" fill="none" stroke="#fff" stroke-width="1.5"/>
        </svg>
        <span>your@mailbox.net.au</span>
      </li>
      <li>
        <svg class="contact__icon" viewBox="0 0 22 22" aria-hidden="true">
          <rect width="22" height="22" rx="3" fill="#1a9ad6"/>
          <circle cx="11" cy="11" r="6.5" fill="none" stroke="#fff" stroke-width="1.3"/>
          <ellipse cx="11" cy="11" rx="3" ry="6.5" fill="none" stroke="#fff" stroke-width="1.1"/>
          <path d="M4.5 11h13M6 7.5h10M6 14.5h10" stroke="#fff" stroke-width="1.1"/>
        </svg>
        <span>www.tallpinecomputing.com</span>
      </li>
    </ul>
  </section>
</body>
</html>
```